Business Card for a New Zealand IT Startup

I need a business card for VELTA Holdings. We are a young startup based in New Zealand working in internet marketing and web development. The design should have some element connected to New Zealand, such as wave, koru or silver fern, just don't use a kiwi bird.

```html
<!DOCTYPE html>
<html lang="en">
<head>
<meta charset="utf-8">
<title>VELTA Holdings – Business Card</title>
<link rel="stylesheet" href="https://fonts.googleapis.com/css2?family=Jost:wght@400;500;600&display=swap">
<style>
  :root {
    --backdrop: #e6e6e6;
    --card-white: #ffffff;
    --brand-blue: #0a6cb8;
    --brand-orange: #f15a24;
    --ink: #4a4a4a;
  }
  * { box-sizing: border-box; margin: 0; padding: 0; }
  html, body {
    width: 1125px; height: 1200px; overflow: hidden;
    background: var(--backdrop);
    font-family: "Jost", Arial, sans-serif;
  }
  .canvas { position: relative; width: 1125px; height: 1200px; }
  .card {
    position: absolute; left: 166px; width: 800px; height: 457px;
    border-radius: 26px; overflow: hidden;
    box-shadow: 0 2px 5px rgba(0,0,0,0.35);
  }
  .card--front { top: 103px; background: var(--card-white); }
  .card--back { top: 620px; background: var(--brand-orange); }
  .wave-bands { position: absolute; inset: 0; }
  .holder {
    position: absolute; left: 66px; top: 227px;
    transform: translate(-50%, -50%) rotate(-90deg);
    color: var(--card-white); white-space: nowrap; text-align: left;
  }
  .holder__name { font-size: 34px; font-weight: 400; line-height: 1; letter-spacing: 0.5px; }
  .holder__role { font-size: 20px; font-weight: 400; line-height: 1.2; }
  .wordmark {
    position: absolute; right: 58px; top: 60px; text-align: right;
    color: var(--brand-blue); font-weight: 600; line-height: 1;
  }
  .wordmark__main { font-size: 86px; letter-spacing: 2px; }
  .wordmark__sub { font-size: 26px; letter-spacing: 13px; margin-top: 12px; margin-right: -13px; }
  .contact {
    position: absolute; right: 58px; top: 240px; text-align: right;
    color: var(--ink); font-size: 19px; line-height: 25px;
  }
  .contact__address { margin-bottom: 12px; }
  .contact__row { display: flex; justify-content: flex-end; align-items: center; gap: 7px; }
  .contact__row svg { width: 18px; height: 18px; fill: var(--brand-blue); }
  .back-mark {
    position: absolute; left: 0; right: 0; top: 96px;
    display: flex; flex-direction: column; align-items: center; gap: 22px;
  }
  .back-mark__dot { width: 150px; height: 150px; border-radius: 50%; background: var(--card-white); }
  .back-mark__name { color: var(--card-white); font-size: 40px; font-weight: 600; letter-spacing: 4px; }
  .back-web {
    position: absolute; left: 0; right: 0; top: 378px; text-align: center;
    color: var(--card-white); font-size: 19px; letter-spacing: 7px;
  }
</style>
</head>
<body>
<main class="canvas">
  <section class="card card--front">
    <svg class="wave-bands" viewBox="0 0 800 457" width="800" height="457" aria-hidden="true">
      <path d="M0 0 H207 C118 110 110 330 219 457 H0 Z" fill="var(--brand-blue)"/>
      <path d="M226 10 C150 120 140 330 226 457" fill="none" stroke="var(--brand-blue)" stroke-width="3"/>
      <path d="M244 0 C150 110 140 330 229 457 L265 457 C175 330 170 110 248 0 Z" fill="var(--brand-orange)"/>
    </svg>
    <div class="holder">
      <div class="holder__name">MARA QUINN</div>
      <div class="holder__role">CEO/FOUNDER</div>
    </div>
    <div class="wordmark">
      <div class="wordmark__main">VELTA</div>
      <div class="wordmark__sub">HOLDINGS</div>
    </div>
    <div class="contact">
      <div class="contact__address">412 Harbour View Road<br>Wellington, New Zealand 6011</div>
      <div class="contact__row">021 455 7310
        <svg viewBox="0 0 24 24"><path d="M6.6 10.8a15 15 0 0 0 6.6 6.6l2.2-2.2c.3-.3.7-.4 1-.2 1.1.4 2.3.6 3.6.6.6 0 1 .4 1 1V20c0 .6-.4 1-1 1A17 17 0 0 1 3 4c0-.6.4-1 1-1h3.5c.6 0 1 .4 1 1 0 1.3.2 2.5.6 3.6.1.3 0 .7-.2 1z"/></svg></div>
      <div class="contact__row">027 638 1942
        <svg viewBox="0 0 24 24"><path d="M7 1h10a2 2 0 0 1 2 2v18a2 2 0 0 1-2 2H7a2 2 0 0 1-2-2V3a2 2 0 0 1 2-2zm0 3v14h10V4zm5 15.5a1 1 0 1 0 0 2 1 1 0 0 0 0-2z"/></svg></div>
      <div class="contact__row">mara@veltaholdings.com
        <svg viewBox="0 0 24 24"><path d="M2 5h20v14H2zm2 2v.5l8 5 8-5V7zm0 3v7h16v-7l-8 5z"/></svg></div>
      <div class="contact__row">www.veltaholdings.com
        <svg viewBox="0 0 24 24"><path d="M12 2a10 10 0 1 0 0 20 10 10 0 0 0 0-20zm0 2c1.2 1.4 2 3.5 2.2 7H9.8C10 7.5 10.8 5.4 12 4zM4.1 11a8 8 0 0 1 4.2-6.1C7.5 6.6 7.9 8.7 7.8 11zm0 2h3.7c.1 2.3.6 4.4 1.5 6.1A8 8 0 0 1 4.1 13zm5.7 0h4.4c-.2 3.5-1 5.6-2.2 7-1.2-1.4-2-3.5-2.2-7zm6.4 0h3.7a8 8 0 0 1-4.2 6.1c.9-1.7 1.4-3.8 1.5-6.1zm0-2c-.1-2.3-.6-4.4-1.5-6.1A8 8 0 0 1 19.9 11z"/></svg></div>
    </div>
  </section>

  <section class="card card--back">
    <div class="back-mark">
      <div class="back-mark__dot"></div>
      <div class="back-mark__name">VELTA HOLDINGS</div>
    </div>
    <div class="back-web">www.veltaholdings.com</div>
  </section>
</main>
</body>
</html>
```